New, modern business card for growing audiology practice

We need a new business card for our audiology practice. Our logo and website have recently changed (more modern) and we want our business cards to reflect this change.
We conduct hearing tests, perform earwax removals, and fit & dispense hearing aids to our patients. We are a family owned practice in which the owner is the one who works directly with the patient. I have attached logos in various formats to use, as well as two ideas I found on this website; as well as a scanned copy of our current logo. Good luck!

Industry/Entity Type

Business

Contact Information for Business Card

Company name: Tolvera Hearing Center
Provider name: Peter Wolstenby, Au.D. F/NSB
Phone number: (555) 683-5127
Address: 837 W. Lindell Ave. Wendmoor Falls, OH 40917
email: tolverahearing@postvane.com
website: tolverahearing.com

Colors
000000
aaaaaa
dbdbdb
cacaca
9bcb3c
afd23c
cadf82
b1b1b1

Requirements
Must have
• My card must include information in the "details" section. In the attached images, I found a few that I liked and I would like to model after - "brisky bouncin'" and "Sound Method Center".
• Must be horizontal.
• Must include logos provided. I uploaded them in various file formats and various ways.
• Must match logo font, if possible, if not, please get as close as you can.
Nice to have
• I really like the idea of having a color on one side with just the logo and company name and the contact information and provider name on the other side. I also really like the idea of having the main color dominating on the logo/company side with accent of that same color on the contact side of the card.
Should not have
• Must not be vertical.

```html
<!DOCTYPE html>
<html lang="en">
<head>
<meta charset="utf-8">
<title>Tolvera Hearing Center – Business Card</title>
<link rel="stylesheet" href="https://fonts.googleapis.com/css2?family=Lato:wght@400&family=Roboto+Condensed:wght@700&family=Roboto:wght@400&display=swap">
<style>
  :root {
    --backdrop: #3a3a3a;
    --card: #1f1f20;
    --white: #f4f4f4;
    --green: #9bcb3c;
    --grey-line: #dbdbdb;
  }
  * { margin: 0; padding: 0; box-sizing: border-box; }
  html, body { width: 1200px; height: 900px; overflow: hidden; }
  body {
    background: var(--backdrop);
    position: relative;
    font-family: "Roboto", Arial, sans-serif;
  }
  .card {
    position: absolute;
    left: 280px;
    width: 640px;
    height: 366px;
    background: var(--card);
    box-shadow: 0 10px 28px rgba(0,0,0,0.45);
  }
  .card--front { top: 70px; }
  .card--back { top: 466px; }

  .brand {
    position: absolute;
    top: 128px;
    left: 0;
    width: 100%;
    display: flex;
    justify-content: center;
    align-items: center;
    gap: 14px;
  }
  .brand__dot {
    width: 22px; height: 22px;
    border-radius: 50%;
    background: var(--green);
  }
  .brand__name {
    font-family: "Lato", Arial, sans-serif;
    font-weight: 400;
    font-size: 31px;
    letter-spacing: 0.5px;
    color: var(--white);
    text-transform: uppercase;
    white-space: nowrap;
  }
  .website {
    position: absolute;
    top: 236px;
    width: 100%;
    text-align: center;
    font-size: 14px;
    letter-spacing: 5px;
    color: var(--white);
  }
  .website__domain { color: var(--green); }

  .provider {
    position: absolute;
    right: 322px;
    top: 140px;
    text-align: right;
    white-space: nowrap;
  }
  .provider__name {
    font-family: "Roboto Condensed", "Arial Narrow", sans-serif;
    font-weight: 700;
    font-size: 36px;
    line-height: 1.05;
    color: var(--green);
    text-transform: uppercase;
  }
  .provider__title {
    font-size: 17px;
    color: var(--white);
    margin-top: 4px;
    letter-spacing: 0.5px;
  }
  .divider {
    position: absolute;
    left: 338px;
    top: 110px;
    width: 2px;
    height: 150px;
    background: linear-gradient(to bottom, rgba(219,219,219,0.9), rgba(219,219,219,0.15));
  }
  .contact {
    position: absolute;
    left: 358px;
    top: 112px;
    color: var(--white);
    font-size: 17px;
    line-height: 1.3;
    white-space: nowrap;
  }
  .contact__address { margin-bottom: 10px; }
  .contact__row {
    display: flex;
    align-items: center;
    gap: 10px;
  }
  .contact__icon { width: 15px; height: 15px; flex: none; }
</style>
</head>
<body>

<section class="card card--front">
  <div class="brand">
    <span class="brand__dot"></span>
    <span class="brand__name">Tolvera Hearing Center</span>
  </div>
  <p class="website">www.<span class="website__domain">tolverahearing</span>.com</p>
</section>

<section class="card card--back">
  <div class="provider">
    <h1 class="provider__name">Peter Wolstenby</h1>
    <p class="provider__title">AU.D. F/NSB</p>
  </div>
  <span class="divider"></span>
  <div class="contact">
    <p class="contact__address">837 W. Lindell Ave.<br>Wendmoor Falls, OH 40917</p>
    <p class="contact__row">
      <svg class="contact__icon" viewBox="0 0 16 16" aria-hidden="true"><path fill="#9bcb3c" d="M3.6 1.2 5.8 3.6 4.6 5.4c.9 2 2.4 3.5 4.4 4.4l1.8-1.2 2.4 2.2-1 2.4C7.1 13.7 2.3 8.9 1.2 3.2z"/></svg>
      (555) 683-5127
    </p>
    <p class="contact__row">
      <svg class="contact__icon" viewBox="0 0 16 16" aria-hidden="true"><rect x="1" y="3.5" width="14" height="9.5" fill="#9bcb3c"/><path d="M1 3.5 8 9l7-5.5" fill="none" stroke="#1f1f20" stroke-width="1.4"/></svg>
      tolverahearing@postvane.com
    </p>
    <p class="contact__row">
      <svg class="contact__icon" viewBox="0 0 16 16" aria-hidden="true"><circle cx="8" cy="8" r="7" fill="#9bcb3c"/><path d="M1 8h14M8 1c-3 3.5-3 10.5 0 14M8 1c3 3.5 3 10.5 0 14" fill="none" stroke="#1f1f20" stroke-width="1.1"/></svg>
      tolverahearing.com
    </p>
  </div>
</section>

</body>
</html>
```